KORV PTY LTD - Business Cards

Design a modern business card - using the attached Designs.
Same design as on the front, apart from the names/numbers/emails to be different.
We want the cards to be very glossy to stand out, do I think the simple black/white/metallic will be effective.
Both lots of details below:

Tom Wrenshaw
Director
tom_korv@nulvane.com
0438 274 093

Lewis Corbyn
Director
lewis_korv@nulvane.com
0419 385 642

Industry/Entity Type

Business

```html
<!DOCTYPE html>
<html lang="en">
<head>
<meta charset="utf-8">
<title>KORV PTY LTD – Business Cards</title>
<link href="https://fonts.googleapis.com/css2?family=Open+Sans:wght@400;600&display=swap" rel="stylesheet">
<style>
  :root {
    --page-bg: #e9e6e2;
    --card-white: #ffffff;
    --ink-dark: #222222;
    --ink-mid: #3a3a3a;
    --divider: #d4d4d4;
    --metal-light: #f4f5f5;
    --metal-mid: #c9cdcf;
    --metal-dark: #9ea6aa;
    --mark-dark: #2e2e2e;
  }
  * { box-sizing: border-box; margin: 0; padding: 0; }
  html, body {
    width: 1200px; height: 475px; overflow: hidden;
    background: var(--page-bg);
    font-family: "Open Sans", Arial, sans-serif;
  }
  .sheet {
    position: relative; width: 1200px; height: 475px;
    display: flex; justify-content: center; align-items: center; gap: 50px;
  }
  .card {
    width: 520px; height: 300px; position: relative;
    box-shadow: 0 6px 18px rgba(0,0,0,.18);
  }
  .card--front { background: var(--card-white); }
  .card--back {
    background: linear-gradient(100deg, var(--metal-mid) 0%, var(--metal-light) 18%, var(--metal-mid) 38%, var(--metal-light) 55%, var(--metal-dark) 100%);
    display: flex; align-items: center; justify-content: center;
  }
  .brand {
    display: flex; align-items: center; gap: 10px;
    font-weight: 600; color: var(--mark-dark); letter-spacing: 2px;
  }
  .brand__dot { border-radius: 50%; background: var(--mark-dark); flex: none; }
  .card--front .brand {
    position: absolute; left: 40px; top: 124px; font-size: 38px;
  }
  .card--front .brand__dot { width: 18px; height: 18px; }
  .card--back .brand { font-size: 92px; gap: 22px; }
  .card--back .brand__dot { width: 44px; height: 44px; }
  .divider {
    position: absolute; left: 262px; top: 78px; width: 1px; height: 144px;
    background: var(--divider);
  }
  .details { position: absolute; left: 290px; top: 82px; color: var(--ink-dark); }
  .details__name { font-size: 20px; font-weight: 600; }
  .details__role { font-size: 13px; color: var(--ink-mid); margin-top: 4px; }
  .details__list { list-style: none; margin-top: 28px; font-size: 14px; color: var(--ink-dark); }
  .details__list li { display: flex; align-items: center; gap: 7px; margin-bottom: 5px; }
  .details__list svg { width: 12px; height: 12px; fill: var(--ink-dark); flex: none; }
</style>
</head>
<body>
<main class="sheet">
  <section class="card card--front" aria-label="Business card front">
    <div class="brand"><span class="brand__dot"></span>KORV</div>
    <div class="divider"></div>
    <div class="details">
      <p class="details__name">Lewis Corbyn</p>
      <p class="details__role">Director</p>
      <ul class="details__list">
        <li>
          <svg viewBox="0 0 24 24" aria-hidden="true"><path d="M6.6 10.8a15.1 15.1 0 0 0 6.6 6.6l2.2-2.2a1 1 0 0 1 1-.25 11.4 11.4 0 0 0 3.6.57 1 1 0 0 1 1 1V20a1 1 0 0 1-1 1A17 17 0 0 1 3 4a1 1 0 0 1 1-1h3.5a1 1 0 0 1 1 1c0 1.25.2 2.45.57 3.57a1 1 0 0 1-.25 1z"/></svg>
          0419 385 642
        </li>
        <li>
          <svg viewBox="0 0 24 24" aria-hidden="true"><path d="M2 9l10-6 10 6v11H2z M4 10l8 5 8-5"/></svg>
          lewis_korv@nulvane.com
        </li>
      </ul>
    </div>
  </section>
  <section class="card card--back" aria-label="Business card back">
    <div class="brand"><span class="brand__dot"></span>KORV</div>
  </section>
</main>
</body>
</html>
```